New Bicycle shop business card

Hi!
I'm looking for a business card for my new proffesional bike mechanics shop. This shop is only for fixing broken bikes and not selling bikes.
Peferbly a modern and sleek and modern design.
Colors: black, grey, red, white
Information:
Name: Rijwielwerkplaats Vanhoutte
Shop owner: Bart Vanhoutte & Marieke Segers
Website: www.rijwielwerkplaats-vanhoutte.be
Email: info@rijwielwerkplaats-vanhoutte.be
Phone number: +32471902368
Street adres: Kerkweg 46
9940 Bellebeke
Slogan/shop information: Herstellingen van alle merken.
Logo: see files.
Target Market(s)
People who seek a mechanic to fix or upgrade their bikes.
Contact Information for Business Card
Information:
Website: info@rijwielwerkplaats-vanhoutte.be
9940 Bellebeke
Logo: see files.

```html
<!DOCTYPE html>
<html lang="nl">
<head>
<meta charset="utf-8">
<title>Rijwielwerkplaats Vanhoutte – Visitekaartje</title>
<link href="https://fonts.googleapis.com/css2?family=Montserrat:wght@600;700&family=Roboto:wght@400&display=swap" rel="stylesheet">
<style>
  :root {
    --page-bg: #d9d6d2;
    --card-bg: #f1f0ee;
    --ink: #2a2a2a;
    --ink-soft: #3c3c3c;
    --red: #c8323d;
    --red-deep: #b02733;
    --grey-line: #8a8a8a;
    --divider: #d4d2cf;
    --band-text: #f3dfe0;
  }
  * { margin: 0; padding: 0; box-sizing: border-box; }
  html, body {
    width: 1200px;
    height: 1054px;
    overflow: hidden;
    background: var(--page-bg);
  }
  .business-card {
    position: absolute;
    left: 100px;
    top: 225px;
    width: 1000px;
    height: 604px;
    background: var(--card-bg);
    box-shadow: 0 10px 30px rgba(0,0,0,0.18);
    overflow: hidden;
  }
  .brand {
    position: absolute;
    left: 0;
    top: 0;
    width: 485px;
    height: 533px;
    display: flex;
    flex-direction: column;
    align-items: center;
    justify-content: center;
    padding-bottom: 20px;
  }
  .brand-mark {
    width: 86px;
    height: 86px;
    border-radius: 50%;
    background: var(--red);
    margin-bottom: 34px;
  }
  .brand-name {
    font-family: "Montserrat", sans-serif;
    font-weight: 700;
    color: var(--ink);
    text-transform: uppercase;
    text-align: center;
    line-height: 1.2;
    font-size: 29px;
    letter-spacing: 1px;
  }
  .brand-name span { display: block; }
  .brand-name .second-line { letter-spacing: 8px; }
  .divider {
    position: absolute;
    left: 485px;
    top: 110px;
    width: 1px;
    height: 330px;
    background: var(--divider);
  }
  .contact {
    position: absolute;
    left: 523px;
    top: 138px;
    right: 20px;
    font-family: "Roboto", sans-serif;
    color: var(--ink-soft);
  }
  .person-name {
    font-family: "Montserrat", sans-serif;
    font-weight: 600;
    color: var(--red);
    font-size: 34px;
    letter-spacing: 1px;
    text-transform: uppercase;
    line-height: 1;
  }
  .person-role {
    font-size: 23px;
    margin-top: 12px;
  }
  .contact-list {
    list-style: none;
    margin-top: 44px;
  }
  .contact-list li {
    display: flex;
    align-items: center;
    font-size: 22px;
    height: 37px;
  }
  .contact-list svg {
    width: 22px;
    height: 22px;
    margin-right: 26px;
    flex: none;
    fill: var(--red);
  }
  .address {
    font-size: 23px;
    margin-top: 14px;
  }
  .rule {
    position: absolute;
    left: 0;
    right: 0;
    top: 531px;
    height: 4px;
    background: var(--grey-line);
  }
  .tagline-band {
    position: absolute;
    left: 0;
    right: 0;
    top: 542px;
    height: 62px;
    background: linear-gradient(180deg, var(--red) 0%, var(--red-deep) 100%);
    display: flex;
    align-items: center;
    justify-content: center;
    font-family: "Roboto", sans-serif;
    font-size: 23px;
    color: var(--band-text);
  }
</style>
</head>
<body>
  <main class="business-card">
    <section class="brand">
      <div class="brand-mark"></div>
      <h1 class="brand-name">
        <span>Rijwielwerkplaats</span>
        <span class="second-line">Vanhoutte</span>
      </h1>
    </section>

    <div class="divider"></div>

    <section class="contact">
      <h2 class="person-name">Marieke Segers</h2>
      <p class="person-role">Owner</p>

      <ul class="contact-list">
        <li>
          <svg viewBox="0 0 24 24" aria-hidden="true">
            <path d="M3 8c0-2 4-4 9-4s9 2 9 4v2h-5V8c-1-.6-2.4-1-4-1s-3 .4-4 1v2H3z"/>
            <path d="M6 12h12l2 7H4z"/>
          </svg>
          +32471902368
        </li>
        <li>
          <svg viewBox="0 0 24 24" aria-hidden="true">
            <path d="M2 5h20v14H2z M4 7v1l8 5 8-5V7l-8 5z" fill-rule="evenodd"/>
          </svg>
          www.rijwielwerkplaats-vanhoutte.be
        </li>
        <li>
          <svg viewBox="0 0 24 24" aria-hidden="true">
            <circle cx="12" cy="12" r="10"/>
            <path d="M2 12h20M12 2c3 3 3 17 0 20M12 2c-3 3-3 17 0 20M4 7h16M4 17h16" stroke="#f1f0ee" stroke-width="1.3" fill="none"/>
          </svg>
          info@rijwielwerkplaats-vanhoutte.be
        </li>
      </ul>

      <p class="address">Kerkweg 46 9940 Bellebeke</p>
    </section>

    <div class="rule"></div>
    <footer class="tagline-band">Herstellingen van alle merken</footer>
  </main>
</body>
</html>
```